We need a new business card that reflects who we are. Professional, classy, modern, and service ori

We need a business card design for a window coverings design company in Kansas City called Bright Lane Interiors. We offer professional, modern, and high quality window covering products. We are looking to portray an image of a big, national franchise. We are a 5 location (with showrooms) business with 10 professional designers and 4 professional installers. These cards will be used with Thank you cards, given to realtors, and asked for referrals with.

Target Market(s)

Kansas City

Industry/Entity Type

Business

Contact Information for Business Card

We would like our card to look clean and simple on the front, featuring our logo and Marlow Fenwick's. Our designers' phone numbers and emails should be displayed as well as their title.

Font styles to use
Sans Serif

Colors

Designer to choose colors to be used in the design.

Requirements
Must have
• Front - Logos, name, phone number, email address
• Back - Showroom locations, social media? Appt date/time?
Nice to have
• I would like a clean and modern look (not contemporary. I like a white background, but I am open to ideas. Looking for a "National chain" look for a small business.
Should not have
• Too much busyness.

```html
<!DOCTYPE html>
<html lang="en">
<head>
<meta charset="utf-8">
<title>Bright Lane Interiors – Business Card</title>
<link rel="stylesheet" href="https://fonts.googleapis.com/css2?family=Roboto:wght@400;500;700&family=Roboto+Condensed:wght@500;700&display=swap">
<style>
  :root {
    --backdrop: #2a2a2a;
    --card: #f3f3f3;
    --brand-red: #c8363d;
    --brand-grey: #9a9b9d;
    --ink: #1a1a1a;
    --text-grey: #555555;
    --band: #111111;
    --partner-grey: #5d6670;
    --partner-accent: #e98a2c;
  }
  * { margin: 0; padding: 0; box-sizing: border-box; }
  html, body { width: 1200px; height: 960px; overflow: hidden; }
  body {
    position: relative;
    background: var(--backdrop);
    font-family: "Roboto", Arial, sans-serif;
  }
  .card {
    position: absolute;
    width: 600px;
    background: var(--card);
  }
  .card--front { left: 314px; top: 113px; height: 330px; }
  .card--back  { left: 311px; top: 472px; height: 343px; }

  .front-band {
    position: absolute; left: 314px; top: 443px;
    width: 600px; height: 13px; background: var(--band);
  }
  .front-band .segment { position: absolute; top: 0; height: 13px; }
  .segment--grey-a { left: 367px; width: 29px; background: var(--brand-grey); }
  .segment--red    { left: 396px; width: 87px; background: var(--brand-red); }
  .segment--grey-b { left: 483px; width: 29px; background: var(--brand-grey); }

  .designer { position: absolute; left: 48px; top: 63px; }
  .designer__name {
    font-family: "Roboto Condensed", Arial, sans-serif;
    font-weight: 700; font-size: 23px; color: var(--brand-red); line-height: 1;
  }
  .designer__title {
    font-weight: 700; font-size: 14.5px; color: var(--ink); margin-top: 4px;
  }

  .brand { position: absolute; right: 48px; text-align: right; }
  .card--front .brand { top: 126px; }
  .brand__name {
    display: flex; align-items: center; justify-content: flex-end; gap: 10px;
    font-weight: 700; font-size: 24px; color: var(--ink); line-height: 1;
  }
  .brand__mark { width: 18px; height: 18px; background: var(--brand-red); flex: none; }
  .brand__tagline { font-size: 12.5px; color: var(--ink); margin-top: 8px; }

  .contact { position: absolute; left: 48px; top: 229px; list-style: none; }
  .contact li {
    display: flex; align-items: center; gap: 8px;
    font-size: 14.5px; color: var(--text-grey); height: 19px;
  }
  .contact svg { width: 13px; height: 13px; flex: none; }

  .card--back .brand { top: 64px; right: 60px; }
  .appointment { position: absolute; left: 43px; top: 87px; width: 500px; }
  .appointment__title { font-size: 21px; font-weight: 500; color: var(--brand-red); }
  .field {
    display: flex; align-items: baseline; margin-top: 29px;
    font-size: 16px; color: var(--brand-red);
  }
  .field + .field { margin-top: 22px; }
  .field__line {
    flex: 1; border-bottom: 1px dotted #444; margin: 0 4px 4px; height: 1px; align-self: flex-end;
  }
  .field__line--short { flex: .7; }
  .field__suffix { font-size: 12px; margin-left: 2px; }
  .locations {
    position: absolute; left: 43px; top: 232px;
    font-weight: 700; font-size: 14.5px; color: var(--text-grey);
  }
  .social { position: absolute; left: 44px; top: 279px; display: flex; gap: 3px; }
  .social span { width: 22px; height: 22px; border-radius: 50%; background: var(--brand-red); }
  .partner {
    position: absolute; right: 56px; top: 280px;
    display: flex; align-items: center; gap: 5px;
    font-size: 14px; font-weight: 500; color: var(--partner-grey);
  }
  .partner__dot { width: 20px; height: 20px; border-radius: 50%; background: var(--partner-accent); }
</style>
</head>
<body>
  <section class="card card--front">
    <div class="designer">
      <div class="designer__name">DANIEL REYES</div>
      <div class="designer__title">DESIGNER</div>
    </div>
    <div class="brand">
      <div class="brand__name"><span class="brand__mark"></span>Bright Lane Interiors</div>
      <div class="brand__tagline">Blinds, Shades, Shutters, Draperies &amp; Decor</div>
    </div>
    <ul class="contact">
      <li><svg viewBox="0 0 16 16"><path fill="#c8363d" d="M3.6 1l2.6 2.6-1.6 2.1c.9 1.9 2.4 3.4 4.3 4.3l2.1-1.6L15.6 11l-1.9 3.2C7.5 14 2 8.5 1.8 2.3z"/></svg>913.555.0148</li>
      <li><svg viewBox="0 0 16 16"><rect x="1" y="3" width="14" height="10" fill="#c8363d"/><path d="M1 3l7 5 7-5" stroke="#f3f3f3" stroke-width="1.2" fill="none"/></svg>info@brightlaneinteriors.com</li>
      <li><svg viewBox="0 0 16 16"><circle cx="8" cy="8" r="7" fill="#c8363d"/><path d="M1 8h14M8 1c-3 4-3 10 0 14M8 1c3 4 3 10 0 14" stroke="#f3f3f3" stroke-width="1" fill="none"/></svg>brightlaneinteriors.com</li>
    </ul>
  </section>
  <div class="front-band">
    <span class="segment segment--grey-a"></span>
    <span class="segment segment--red"></span>
    <span class="segment segment--grey-b"></span>
  </div>

  <section class="card card--back">
    <div class="brand">
      <div class="brand__name"><span class="brand__mark"></span>Bright Lane Interiors</div>
    </div>
    <div class="appointment">
      <h2 class="appointment__title">Next Appointment</h2>
      <div class="field">Name :<span class="field__line"></span></div>
      <div class="field">Date :<span class="field__line"></span>Time :<span class="field__line field__line--short"></span><span class="field__suffix">AM/PM</span></div>
    </div>
    <div class="locations">WESTBROOK | CEDAR HEIGHTS | MAPLE RIDGE | NORTHGATE | PINE HOLLOW</div>
    <div class="social"><span></span><span></span><span></span><span></span></div>
    <div class="partner"><span>Marlow Fenwick Gallery</span><span class="partner__dot"></span></div>
  </section>
</body>
</html>
```